Give Gold Kite an Online Presence!

Gold Kite Property Maintenance is an Australian Owned property maintenance company who needs a stand out online presence.

GK maintains many buildings and sites and wants to appeal to a corporate professional market with their brand new website. GK is essentially a handyman service offering all maintenance services to home owners, office managers, real estate agents and strata managers.

The Website:
We need a corporate website that appeals to our broader customer base (property owners, property managers, office managers) the copy is being written by a professional so use filler text for now.

Things that we want:
Home page that sets us apart and appeals to the corporate and residential market. The home page needs to not focus on either the residential or commercial market. The home page should focus on our logo and branding. We have a logo already and it is attached to the brief, please use it and try to consider the colour pallette that goes with it. Whilst we want the site to appear strong and manly it is important to remember that 95% of our customers are female so we need the site to be appealing to women. Women need to believe that we are strong, dependable and trustworthy.
We'd like a quote page and potentially also the ability to get a quote from the home page (please don't put it in if it ruins the overall feel of the home page)
An "about us" page
A contact us page
A blog that's built in (we don't want to link to an external blog)
(overall we'd expect to have 6 or 7 pages total)

The site will also need coding - we expect this to be done in a separate project but need you to consider a few things about the coding side of things.

It needs to be iPhone and iPad compatible.

We'd like you to suggest the best CMS that you would use or if you would suggest not using a CMS please let us know with your submissions.

Target Market(s)

Property owners, office managers and property managers who need maintenance on buildings (So all of them)

Industry/Entity Type

Property Maintenance

Requirements
Must have
• Our Logo
Home page
About Us
Residential
Commercial
Real Estate/Strata
Contact Us/Quote
Blog
Nice to have
• Quote form included in home page
Movement on the home page at least
Should not have
• other logos, too much colour
NO FLASH

```html
<!DOCTYPE html>
<html lang="en">
<head>
<meta charset="utf-8">
<title>Gold Kite Property Maintenance</title>
<link rel="stylesheet" href="https://fonts.googleapis.com/css2?family=Lato:wght@300;400;700;900&display=swap">
<style>
  :root {
    --ink: #2b2b2b;
    --ink-soft: #444444;
    --panel: #f7f7f7;
    --panel-line: #e6e6e6;
    --gold: #d89200;
    --band-top: #4a78c0;
    --band-dark: #2e4f8c;
    --band-bottom: #4373c2;
    --band-text: #eef2fa;
    --band-muted: #b9c9e6;
    --band-rule: rgba(255, 255, 255, 0.28);
    --button-light: #6c6c6c;
    --button-dark: #2c2c2c;
    --white: #ffffff;
  }
  * { box-sizing: border-box; margin: 0; padding: 0; }
  html, body {
    width: 1200px;
    height: 819px;
    overflow: hidden;
    background: var(--white);
    font-family: 'Lato', Arial, sans-serif;
  }
  .page {
    position: relative;
    width: 1200px;
    height: 819px;
    overflow: hidden;
    background: var(--white);
  }
  .blue-band {
    position: absolute;
    left: 0; top: 404px;
    width: 1200px; height: 415px;
    background: linear-gradient(to bottom,
      var(--band-top) 0px,
      var(--band-dark) 14px,
      #33579a 90px,
      #3e69b3 200px,
      var(--band-bottom) 415px);
  }
  .main-nav {
    position: absolute;
    top: 18px; right: 88px;
    display: flex;
    align-items: center;
    font-size: 14.5px;
    color: var(--ink);
  }
  .main-nav a { color: var(--ink); text-decoration: none; }
  .main-nav .divider { margin: 0 23px; color: var(--ink); }

  .brand-name {
    position: absolute;
    left: 100px; top: 296px;
    width: 460px;
    text-align: center;
    font-weight: 900;
    font-size: 40px;
    line-height: 48px;
    color: var(--gold);
    text-transform: uppercase;
    letter-spacing: 0.5px;
  }

  .contact-panel {
    position: absolute;
    left: 592px; top: 92px;
    width: 510px; height: 269px;
    background: var(--panel);
    border-radius: 6px;
  }
  .contact-row {
    position: absolute;
    left: 30px;
    display: flex;
    align-items: center;
    font-size: 20.5px;
    letter-spacing: 1.1px;
    color: var(--ink);
  }
  .contact-row svg { width: 26px; height: 22px; margin-right: 28px; }
  .contact-row.phone { top: 40px; }
  .contact-row.email { top: 88px; }
  .contact-divider {
    position: absolute;
    left: 0; right: 0; top: 150px;
    border-top: 1px solid var(--panel-line);
  }
  .enter-button {
    position: absolute;
    left: 108px; top: 181px;
    width: 284px; height: 62px;
    border-radius: 5px;
    background: linear-gradient(to bottom, var(--button-light), var(--button-dark));
    box-shadow: 0 2px 3px rgba(0,0,0,0.35);
    display: flex;
    align-items: center;
    justify-content: center;
    color: var(--white);
    font-size: 20px;
    letter-spacing: 0.4px;
    text-decoration: none;
  }
  .enter-button svg { width: 26px; height: 26px; margin-left: 22px; }

  .welcome {
    position: absolute;
    left: 94px; top: 524px;
    width: 722px;
  }
  .welcome h1 {
    font-weight: 300;
    font-size: 38px;
    color: var(--white);
    line-height: 48px;
    padding-bottom: 20px;
    border-bottom: 1px solid var(--band-rule);
  }
  .welcome p {
    margin-top: 22px;
    font-size: 12.4px;
    line-height: 22.8px;
    color: var(--band-text);
    text-align: justify;
  }

  .photo-frame {
    position: absolute;
    left: 839px; top: 532px;
    width: 270px; height: 193px;
    background: var(--white);
    border-radius: 4px;
    padding: 4px;
  }
  .photo-fill {
    width: 100%; height: 100%;
    background: linear-gradient(160deg, #f1ede3 0%, #dcd6c8 45%, #b9b2a4 75%, #6d7f9b 100%);
  }

  .site-footer {
    position: absolute;
    left: 90px; top: 757px;
    width: 1023px;
    border-top: 1px solid var(--band-rule);
    text-align: center;
    padding-top: 20px;
    font-size: 11.5px;
    color: var(--band-muted);
  }
  .site-footer .rights { margin-left: 12px; }
</style>
</head>
<body>
<div class="page">
  <div class="blue-band"></div>

  <nav class="main-nav">
    <a href="#">Home</a><span class="divider">|</span>
    <a href="#">About Us</a><span class="divider">|</span>
    <a href="#">Contact Us</a>
  </nav>

  <div class="brand-name">Gold Kite<br>Property Maintenance</div>

  <section class="contact-panel">
    <div class="contact-row phone">
      <svg viewBox="0 0 26 22" aria-hidden="true">
        <path d="M5 3 C3 5 3 9 6 13 C9 17 13 19 16 19 L18 16 L14 13 L12 14 C10 13 8 11 7 9 L8 7 L6 3 Z" fill="#333"/>
        <path d="M17 4 C20 5 22 7 23 10" stroke="#999" stroke-width="1.6" fill="none"/>
        <path d="M17 7 C19 8 20 9 20.5 11" stroke="#999" stroke-width="1.6" fill="none"/>
      </svg>
      <span>Call us : 555 210 4387</span>
    </div>
    <div class="contact-row email">
      <svg viewBox="0 0 26 22" aria-hidden="true">
        <path d="M2 9 L13 2 L24 9 L24 20 L2 20 Z" fill="#333"/>
        <path d="M5 8 L21 8 L21 12 L13 16 L5 12 Z" fill="#fff"/>
        <path d="M2 9 L13 16 L24 9" stroke="#fff" stroke-width="1.4" fill="none"/>
      </svg>
      <span>E-Mail :&nbsp; info@goldkitehandyman.com</span>
    </div>
    <div class="contact-divider"></div>
    <a class="enter-button" href="#">
      ENTER WEBSITE
      <svg viewBox="0 0 26 26" aria-hidden="true">
        <circle cx="13" cy="13" r="12" fill="#fff"/>
        <path d="M10 7.5 L18.5 13 L10 18.5 Z" fill="#2f2f2f"/>
      </svg>
    </a>
  </section>

  <section class="welcome">
    <h1>Welcome to our site</h1>
    <p>Nemo enim ipsam voluptatem quia voluptas sit aspernatur aut odit aut fugit, sed quia consequuntur magni dolores eos qui ratione voluptatem sequi nesciunt.&nbsp; Neque porro quisquam est, qui dolorem ipsum quia dolor sit amet, consectetur, adipisci velit, sed quia non numquam eius modi tempora incidunt ut labore et dolore magnam aliquam quaerat voluptatem. Ut enim ad minima veniam, quis nostrum exercitationem ullam corporis suscipit laboriosam, nisi ut aliquid ex ea commodi consequatur. Quis autem vel eum iure reprehenderit qui in ea voluptate velit esse quam nihil molestiae consequatur</p>
  </section>

  <figure class="photo-frame">
    <div class="photo-fill" role="img" aria-label="Photo of a tradesman in a blue work shirt fixing a ceiling light in a bright room while a homeowner looks on"></div>
  </figure>

  <footer class="site-footer">
    Copyright © 2012 www.goldkitehandyman.com <span class="rights">All rights reserved.</span>
  </footer>
</div>
</body>
</html>
```